RWT Fittings Ltd Business Cards

We need a business card with our business logo. We provide window and door installations on high-rises in west coast British Colombia, Canada.

I would like my business information and details on one side of the card, and the other side the company name with logo

Target Market(s)

General Contractors

Industry/Entity Type

Construction

Contact Information for Business Card

one side i want my company name and logo in the dark theme logo that i provided

Requirements
Must have
• Marco Peltieri, 16045518293, RWTFittings@mailbox-demo.com, 1407-5194 Linden Row Burnaby BC, V5H 2K9, Owner & Manager

```html
<!DOCTYPE html>
<html lang="en">
<head>
<meta charset="utf-8">
<title>RWT Fittings Ltd – Business Cards</title>
<link rel="stylesheet" href="https://fonts.googleapis.com/css2?family=Montserrat:wght@700;800&family=Roboto:wght@400;500&display=swap">
<style>
  :root {
    --bg: #232323;
    --card-dark: #1e1e21;
    --card-band: #26262a;
    --card-band-2: #2c2c30;
    --brand-blue: #22a3de;
    --pattern-blue: #27a7e0;
    --pattern-light: #6cc8ee;
    --grey: #9a9a9c;
    --white: #ffffff;
  }
  * { box-sizing: border-box; margin: 0; padding: 0; }
  html, body { width: 1200px; height: 780px; overflow: hidden; background: var(--bg); }
  .stage {
    position: relative; width: 1200px; height: 780px;
    display: flex; justify-content: center; align-items: center; gap: 90px;
  }
  .card {
    position: relative; width: 366px; height: 640px; border-radius: 22px; overflow: hidden;
    box-shadow: 0 18px 40px rgba(0,0,0,.55);
  }

  /* Back side */
  .card--back { background: var(--pattern-blue); }
  .card--back .pattern-fill {
    position: absolute; inset: 0;
    background: linear-gradient(160deg, var(--pattern-blue) 0%, #2bb0e6 55%, var(--pattern-light) 140%);
  }
  .back-brand {
    position: absolute; top: 44px; right: 34px;
    display: flex; align-items: center; gap: 8px;
    font-family: "Montserrat", sans-serif; font-weight: 800; font-size: 15px;
    color: var(--white); letter-spacing: .02em;
  }
  .back-brand .mark { width: 12px; height: 12px; background: var(--white); }

  /* Front side */
  .card--front { background: var(--card-dark); }
  .card--front .bands { position: absolute; inset: 0; }
  .front-brand {
    position: absolute; top: 80px; left: 0; right: 0; text-align: center;
    display: flex; justify-content: center; align-items: center; gap: 10px;
    font-family: "Montserrat", sans-serif; font-weight: 800; font-size: 27px;
    color: var(--brand-blue); letter-spacing: .01em;
  }
  .front-brand .mark { width: 22px; height: 22px; background: var(--brand-blue); }

  .person { position: absolute; top: 300px; left: 0; right: 0; text-align: center; }
  .person__name {
    font-family: "Montserrat", sans-serif; font-weight: 800; font-size: 30px; line-height: 1;
  }
  .person__first { color: var(--brand-blue); }
  .person__last { color: var(--grey); }
  .person__role {
    margin-top: 4px; font-family: "Montserrat", sans-serif; font-weight: 700;
    font-size: 13px; color: var(--white);
  }

  .icon-row { display: flex; justify-content: center; gap: 12px; margin-top: 12px; }
  .icon {
    width: 26px; height: 26px; border-radius: 50%; background: var(--brand-blue);
    display: flex; align-items: center; justify-content: center;
  }
  .icon svg { width: 15px; height: 15px; }

  .contact {
    margin-top: 10px; font-family: "Roboto", sans-serif; font-size: 14.5px;
    color: var(--white); line-height: 1.45;
  }

  .address {
    position: absolute; top: 528px; left: 0; right: 0; text-align: center;
    font-family: "Roboto", sans-serif; font-size: 15px; color: var(--white); line-height: 1.4;
  }
  .address .icon { margin: 0 auto 10px; }
</style>
</head>
<body>
<main class="stage">

  <section class="card card--back" aria-label="Card back">
    <div class="pattern-fill" role="img" aria-label="Repeating pattern of the company emblem on bright blue"></div>
    <div class="back-brand"><span class="mark"></span>RWT Fittings Ltd</div>
  </section>

  <section class="card card--front" aria-label="Card front">
    <svg class="bands" viewBox="0 0 366 640" preserveAspectRatio="none" aria-hidden="true">
      <path d="M0 420 C 90 470 190 500 366 470 L366 640 L0 640 Z" fill="var(--card-band-2)"/>
      <path d="M366 300 C 350 420 250 480 110 480 L0 480 L0 640 L366 640 Z" fill="var(--card-band)"/>
      <path d="M366 430 C 280 440 200 470 150 520 C 110 560 60 600 0 620 L0 640 L366 640 Z" fill="#222226"/>
    </svg>

    <div class="front-brand"><span class="mark"></span>RWT Fittings Ltd</div>

    <div class="person">
      <p class="person__name"><span class="person__first">Marco</span> <span class="person__last">Peltieri</span></p>
      <p class="person__role">Owner &amp; Manager</p>
      <div class="icon-row">
        <span class="icon" aria-label="Phone">
          <svg viewBox="0 0 24 24"><path fill="#fff" d="M6.6 10.8a15 15 0 0 0 6.6 6.6l2.2-2.2c.3-.3.7-.4 1-.2 1.1.4 2.3.6 3.6.6.6 0 1 .4 1 1V20c0 .6-.4 1-1 1A17 17 0 0 1 3 4c0-.6.4-1 1-1h3.5c.6 0 1 .4 1 1 0 1.3.2 2.5.6 3.6.1.3 0 .7-.2 1z"/></svg>
        </span>
        <span class="icon" aria-label="Email">
          <svg viewBox="0 0 24 24"><path fill="#fff" d="M3 6h18v12H3z"/><path d="M3 6l9 7 9-7" fill="none" stroke="#22a3de" stroke-width="2"/></svg>
        </span>
      </div>
      <p class="contact">1604 551 8293<br>RWTFittings@mailbox-demo.com</p>
    </div>

    <div class="address">
      <span class="icon" aria-label="Location">
        <svg viewBox="0 0 24 24"><path fill="#fff" d="M12 2a7 7 0 0 0-7 7c0 5 7 13 7 13s7-8 7-13a7 7 0 0 0-7-7zm0 9.5A2.5 2.5 0 1 1 12 6.5a2.5 2.5 0 0 1 0 5z"/></svg>
      </span>
      <p>1407-5194 Linden Row<br>Burnaby BC, V5H 2K9</p>
    </div>
  </section>

</main>
</body>
</html>
```